Commercial Refrigeration Service Company requires stylish and fresh looking flyer.

We need a flyer to hand out to new customers. It should have a photo and our branding, list all the services that are offered and our contact details.
We would like two flyers to be supplied, both identical though one offering a discount until July ( Half Price Service Fee ). The flyer should be clear, interesting and in similar colours to the branding package supplied.
Please look at our website for information about the services on offer:
www.brisko-coolworks.com.au

Target Market(s)

Cafes, bars, restaurants, pubs ect.

Font styles to use
Other font styles liked:
• Font package provided

Colors
85cae6
ffffff
333333

Requirements
Must have
• - The photo provided.
• - The company logo.
• - Similar feel to the website & business card.
• - Smooth layout and clear to understand.
Should not have
• - No clunky badges or prints.

```html
<!DOCTYPE html>
<html lang="en">
<head>
<meta charset="utf-8">
<title>Brisko Coolworks – Commercial Refrigeration Flyer</title>
<link rel="stylesheet" href="https://fonts.googleapis.com/css2?family=Abel&family=Montserrat:wght@600&display=swap">
<style>
  :root {
    --brand-blue: #85cae6;
    --header-blue: #5bc6f0;
    --accent-blue: #4bbbe8;
    --ink: #333333;
    --paper: #ffffff;
    --paper-shade: #efefef;
    --icon-grey: #8f8f8f;
    --stage: #4a4a4a;
  }
  * { margin: 0; padding: 0; box-sizing: border-box; }
  html, body { width: 1200px; height: 1146px; overflow: hidden; }
  body { background: var(--stage); font-family: "Abel", sans-serif; color: var(--ink); }

  .flyer {
    position: absolute; left: 195px; top: 0;
    width: 810px; height: 1146px;
    background: linear-gradient(180deg, var(--paper) 0%, var(--paper-shade) 100%);
    overflow: hidden;
  }
  .brand-header {
    position: absolute; left: 0; top: 0; width: 100%; height: 163px;
    background: var(--header-blue);
    display: flex; align-items: center; justify-content: center;
  }
  .brand-name {
    font-size: 48px; letter-spacing: 2px; line-height: 1;
    color: var(--ink); font-weight: 400;
  }
  .centered { position: absolute; left: 0; width: 100%; text-align: center; line-height: 1; font-weight: 400; }
  .tagline { top: 194px; font-size: 24px; letter-spacing: 1px; }

  .offer-title { top: 278px; font-size: 44px; color: var(--accent-blue); }
  .offer-sub { top: 325px; font-size: 26px; color: var(--accent-blue); }
  .divider { top: 368px; display: flex; justify-content: center; gap: 20px; }
  .divider span {
    width: 7px; height: 7px; border: 1.4px solid var(--accent-blue); transform: rotate(45deg);
  }

  .services-title { top: 406px; font-size: 28px; color: var(--accent-blue); }
  .services-list { top: 436px; font-size: 22px; line-height: 27px; }

  .service-icons {
    top: 517px; display: flex; justify-content: center; gap: 8px;
  }
  .service-icons svg { width: 64px; height: 64px; }
  .service-icons .disc { fill: var(--icon-grey); stroke: var(--brand-blue); stroke-width: 2.5; }
  .service-icons .glyph { fill: none; stroke: var(--paper); stroke-width: 1.6; stroke-linecap: round; stroke-linejoin: round; }

  .contact-phone { top: 609px; font-size: 29px; }
  .contact-email { top: 644px; font-size: 29px; }

  .photo {
    position: absolute; left: 0; top: 699px; width: 100%; height: 384px;
    background: linear-gradient(180deg, #c9d9e6 0%, #aebfcc 30%, #7b8088 55%, #a7a6a2 100%);
  }
  .site-footer {
    position: absolute; left: 0; top: 1083px; width: 100%; height: 63px;
    background: var(--ink);
    display: flex; align-items: center; justify-content: center;
    font-family: "Montserrat", sans-serif; font-weight: 600;
    font-size: 24px; color: var(--accent-blue); letter-spacing: 0.3px;
  }
</style>
</head>
<body>
  <main class="flyer">
    <header class="brand-header">
      <h1 class="brand-name">Brisko Coolworks</h1>
    </header>

    <p class="centered tagline">Commercial Refrigeration</p>

    <h2 class="centered offer-title">DISCOUNT UNTIL JULY</h2>
    <p class="centered offer-sub">PAY ONLY HALF PRICE OF THE SERVICE FEE</p>
    <div class="centered divider"><span></span><span></span><span></span></div>

    <h3 class="centered services-title">SERVICES</h3>
    <p class="centered services-list">Commercial Refrigeration | Ice Makers | Beer Systems<br>Electrical | 24hr Service | Sales | Installation</p>

    <div class="centered service-icons">
      <svg viewBox="0 0 60 60" aria-label="Refrigeration"><circle class="disc" cx="30" cy="30" r="28"/><g class="glyph"><path d="M27 14v20a5 5 0 1 0 6 0V14a3 3 0 0 0-6 0z"/><path d="M36 18h4M36 22h3M36 26h4M36 30h3"/></g></svg>
      <svg viewBox="0 0 60 60" aria-label="Ice makers"><circle class="disc" cx="30" cy="30" r="28"/><g class="glyph"><path d="M19 17h22l-3 27H22z"/><path d="M20 23h20"/><rect x="25" y="28" width="6" height="6"/><rect x="30" y="34" width="6" height="6"/></g></svg>
      <svg viewBox="0 0 60 60" aria-label="Beer systems"><circle class="disc" cx="30" cy="30" r="28"/><g class="glyph"><path d="M31 14l4 3-6 10"/><path d="M21 29h14v8h-6v5h-4v-5h-4z"/><path d="M35 39v4"/></g></svg>
      <svg viewBox="0 0 60 60" aria-label="Electrical"><circle class="disc" cx="30" cy="30" r="28"/><path class="glyph" d="M33 13L22 32h8l-3 15 11-20h-8z"/></svg>
      <svg viewBox="0 0 60 60" aria-label="24 hour service"><circle class="disc" cx="30" cy="30" r="28"/><g class="glyph"><path d="M18 42l16-16"/><path d="M34 26a6 6 0 1 0 6-8l-4 4-2-2 4-4"/><path d="M19 18l23 23"/><path d="M17 20l3-3 3 3-3 3z"/></g></svg>
      <svg viewBox="0 0 60 60" aria-label="Sales"><circle class="disc" cx="30" cy="30" r="28"/><g class="glyph"><path d="M13 20h5l4 16h20l3-12H20"/><circle cx="24" cy="41" r="2.5"/><circle cx="39" cy="41" r="2.5"/></g></svg>
      <svg viewBox="0 0 60 60" aria-label="Installation"><circle class="disc" cx="30" cy="30" r="28"/><g class="glyph"><path d="M17 38l21-21 5 5-21 21-6 1z"/><path d="M20 18l22 22-4 4-22-22z"/><path d="M24 26l2-2M28 30l2-2M32 34l2-2"/></g></svg>
    </div>

    <p class="centered contact-phone">0412 587 304</p>
    <p class="centered contact-email">info@brisko-coolworks.com.au</p>

    <div class="photo" role="img" aria-label="Photo of the technician standing beside the branded service ute parked at the beach"></div>

    <footer class="site-footer">WWW.BRISKO-COOLWORKS.COM.AU</footer>
  </main>
</body>
</html>
```